Vacation Rental Postcard Design

The Kingfisher's Perch is a vacation rental cottage. We want a postcard that can be used as promotional give-aways for visitors as well as something that can be given to the tourism board and local merchants to help us promote the rental.

Our tag line is" The Kingfisher's Perch - the finest perch on the ridge!". Should also include "Snohomish, WA USA"

We have also used "Come see what all of the buzz is about"

Want to include our info in small print on the mailing side portion of the postcard:

KLWT: www.klwtstays.example/417294
Chatterly: www.chatterly.example/thefinestperchontheridge

Target Market(s)

Couples, romantic, honeymooners, coming for wine tasting, hot air ballooning, hiking, enjoying nature

Industry/Entity Type

Tourism

```html
<!DOCTYPE html>
<html lang="en">
<head>
<meta charset="utf-8">
<title>The Kingfisher's Perch – Postcard Concepts</title>
<link rel="stylesheet" href="https://fonts.googleapis.com/css2?family=Bebas+Neue&family=Poppins:wght@600;700&family=Roboto+Condensed:wght@400&display=swap">
<style>
  :root {
    --page: #ffffff;
    --card: #ffffff;
    --ink: #111111;
    --guide: #d6d6d6;
    --shadow: rgba(0, 0, 0, 0.16);
    --photo-wood: #6a4a32;
    --photo-green: #5f7a4e;
    --photo-sky: #8fa9c8;
    --photo-warm: #a07850;
    --photo-room: #7b5a3c;
    --photo-bed: #b7a58a;
  }
  * { box-sizing: border-box; margin: 0; padding: 0; }
  html, body {
    width: 1200px;
    height: 501px;
    overflow: hidden;
    background: var(--page);
  }
  .board { position: relative; width: 1200px; height: 501px; }

  .postcard {
    position: absolute;
    background: var(--card);
    box-shadow: 0 2px 8px var(--shadow);
    overflow: hidden;
  }
  .postcard--bebas { left: 33px; top: 38px; width: 530px; height: 409px; }
  .postcard--geometric { left: 632px; top: 42px; width: 531px; height: 408px; }

  .postcard__guides { position: absolute; inset: 0; width: 100%; height: 100%; }
  .postcard__guides line { stroke: var(--guide); stroke-width: 1; stroke-dasharray: 6 4; }

  .headline {
    position: absolute;
    color: var(--ink);
    text-transform: uppercase;
    white-space: nowrap;
  }
  .postcard--bebas .headline {
    left: 32px; top: 33px;
    font-family: "Bebas Neue", "Oswald", sans-serif;
    font-weight: 400;
    font-size: 50px;
    line-height: 46px;
    letter-spacing: 2.4px;
  }
  .postcard--geometric .headline {
    left: 33px; top: 36px;
    font-family: "Poppins", "Helvetica Neue", sans-serif;
    font-weight: 700;
    font-size: 36px;
    line-height: 41px;
    letter-spacing: 1.8px;
  }

  .photo-grid {
    position: absolute;
    left: 27px; top: 238px;
    width: 279px; height: 139px;
    display: grid;
    grid-template-columns: repeat(3, 1fr);
    grid-template-rows: repeat(2, 1fr);
    gap: 3px;
  }
  .photo-grid__cell { width: 100%; height: 100%; }
  .photo-grid__cell--cottage { background: linear-gradient(160deg, var(--photo-green), var(--photo-wood)); }
  .photo-grid__cell--meadow { background: linear-gradient(180deg, var(--photo-sky), var(--photo-green)); }
  .photo-grid__cell--balloons { background: linear-gradient(180deg, var(--photo-sky), #c98a4a 70%, var(--photo-green)); }
  .photo-grid__cell--living { background: linear-gradient(160deg, var(--photo-room), var(--photo-warm)); }
  .photo-grid__cell--dining { background: linear-gradient(160deg, var(--photo-warm), #9a8a78); }
  .photo-grid__cell--bedroom { background: linear-gradient(160deg, var(--photo-bed), var(--photo-room)); }

  .contact-line {
    position: absolute;
    writing-mode: vertical-rl;
    transform: rotate(180deg);
    font-family: "Roboto Condensed", "Arial Narrow", sans-serif;
    font-size: 8.4px;
    color: var(--ink);
    white-space: nowrap;
    text-align: center;
  }
  .postcard--bebas .contact-line { left: 331px; top: 36px; height: 338px; }
  .postcard--geometric .contact-line { left: 323px; top: 36px; height: 338px; }
  .contact-line__dot { font-size: 10px; }

  .stamp-box {
    position: absolute;
    width: 73px; height: 91px;
    border: 1px solid var(--ink);
  }
  .postcard--bebas .stamp-box { left: 431px; top: 39px; }
  .postcard--geometric .stamp-box { left: 430px; top: 40px; }

  .brand {
    position: absolute;
    color: var(--ink);
  }
  .brand__mark {
    display: flex;
    align-items: center;
    gap: 6px;
  }
  .brand__dot {
    width: 14px; height: 14px;
    border-radius: 50%;
    background: var(--ink);
    flex: none;
  }
  .brand__tagline,
  .brand__place {
    font-family: "Roboto Condensed", "Arial Narrow", sans-serif;
    font-size: 9.5px;
    line-height: 12px;
    padding-left: 20px;
  }
  .brand__tagline { margin-top: 6px; }
  .postcard--bebas .brand {
    left: 376px; top: 196px; width: 132px;
  }
  .postcard--bebas .brand__mark {
    font-family: "Bebas Neue", "Oswald", sans-serif;
    font-size: 20px; line-height: 20px;
    letter-spacing: 0.6px;
  }
  .postcard--geometric .brand {
    left: 403px; top: 170px; width: 112px;
  }
  .postcard--geometric .brand__mark {
    font-family: "Poppins", "Helvetica Neue", sans-serif;
    font-weight: 700;
    font-size: 11.5px; line-height: 14px;
  }

  .address-lines { position: absolute; }
  .address-lines__rule { height: 20px; border-bottom: 1px solid var(--ink); }
  .postcard--bebas .address-lines { left: 373px; top: 305px; width: 132px; }
  .postcard--geometric .address-lines { left: 373px; top: 292px; width: 132px; }
</style>
</head>
<body>
<main class="board">

  <section class="postcard postcard--bebas" aria-label="Postcard mailing side, condensed headline with photo grid">
    <svg class="postcard__guides" viewBox="0 0 530 409" preserveAspectRatio="none" aria-hidden="true">
      <line x1="0" y1="0" x2="530" y2="409"/>
      <line x1="530" y1="0" x2="0" y2="409"/>
    </svg>
    <h1 class="headline">Come see<br>what all<br>of the buzz<br>is about</h1>
    <div class="photo-grid">
      <div class="photo-grid__cell photo-grid__cell--cottage" role="img" aria-label="Photo of the cottage exterior with garden"></div>
      <div class="photo-grid__cell photo-grid__cell--meadow" role="img" aria-label="Photo of a meadow under a rainbow sky"></div>
      <div class="photo-grid__cell photo-grid__cell--balloons" role="img" aria-label="Photo of hot air balloons over a field"></div>
      <div class="photo-grid__cell photo-grid__cell--living" role="img" aria-label="Photo of the living room with wood floors"></div>
      <div class="photo-grid__cell photo-grid__cell--dining" role="img" aria-label="Photo of the dining area with flowers"></div>
      <div class="photo-grid__cell photo-grid__cell--bedroom" role="img" aria-label="Photo of the bedroom"></div>
    </div>
    <p class="contact-line">www.klwtstays.example/417294 &nbsp;<span class="contact-line__dot">•</span>&nbsp; www.chatterly.example/thefinestperchontheridge</p>
    <div class="stamp-box" aria-label="Stamp area"></div>
    <div class="brand">
      <div class="brand__mark"><span class="brand__dot"></span><span class="brand__name">The Kingfisher's Perch</span></div>
      <p class="brand__tagline">the finest perch on the ridge!</p>
      <p class="brand__place">Snohomish, WA USA</p>
    </div>
    <div class="address-lines" aria-label="Address lines">
      <div class="address-lines__rule"></div>
      <div class="address-lines__rule"></div>
      <div class="address-lines__rule"></div>
    </div>
  </section>

  <section class="postcard postcard--geometric" aria-label="Postcard mailing side, geometric headline">
    <svg class="postcard__guides" viewBox="0 0 531 408" preserveAspectRatio="none" aria-hidden="true">
      <line x1="0" y1="0" x2="531" y2="408"/>
      <line x1="531" y1="0" x2="0" y2="408"/>
    </svg>
    <h2 class="headline">Come see<br>what all<br>of the buzz<br>is about</h2>
    <p class="contact-line">www.klwtstays.example/417294 &nbsp;<span class="contact-line__dot">•</span>&nbsp; www.chatterly.example/thefinestperchontheridge</p>
    <div class="stamp-box" aria-label="Stamp area"></div>
    <div class="brand">
      <div class="brand__mark"><span class="brand__dot"></span><span class="brand__name">The Kingfisher's Perch</span></div>
      <p class="brand__tagline">the finest perch on the ridge!</p>
      <p class="brand__place">Snohomish, WA USA</p>
    </div>
    <div class="address-lines" aria-label="Address lines">
      <div class="address-lines__rule"></div>
      <div class="address-lines__rule"></div>
      <div class="address-lines__rule"></div>
    </div>
  </section>

</main>
</body>
</html>
```